Camp Thornbrook 2021 Magazine Design

We are for someone to design our annual magazine/newsletter. This is a print newsletter that is a total of 20 pages. It will need to be designed in a way that is easy to share with our printers. The designer will need to be someone who is creative and easy to work with.
For those interested in this project we ask that you design 4 to 6 pages for us to view. Once we select the designer we will want the rest created in a two-week time span. For those submitting a bid please include front cover, theme & dates, mission & vision, and Make the Difference.

This link will provide the layout of the newsletter https://files.parcelvault.example/doc/7qzRk2LmVt9XwPa4NbHc6DsYe3FuJg8KoTiW5rQx/edit?share=1.

This link will provide you with the pictures that are needed and a few documents https://files.parcelvault.example/folders/4TpWx8QnRb2ZyLc7MfVd5HsJ?share=1

Details:
20 pages long (including covers)
8.5 x 11

Please message me if you need any further details.

Target Market(s)

Our alumni base. Covers all ages

Requirements
Must have
• Spelled out in document
Nice to have
• Spelled out in document
Should not have
• Spelled out in document

```html
<!DOCTYPE html>
<html lang="en">
<head>
<meta charset="utf-8">
<title>Camp Thornbrook 2021 Magazine</title>
<link href="https://fonts.googleapis.com/css2?family=Oswald:wght@500;700&family=Open+Sans:ital,wght@0,400;0,600;1,400&family=Abril+Fatface&display=swap" rel="stylesheet">
<style>
:root{
  --bg:#e7e3dc;
  --page-top:#ffffff;
  --page-mid:#e4efcf;
  --page-low:#9ec36a;
  --ink:#1f3b12;
  --title-blue:#1c3f9a;
  --title-green:#2f7d1f;
  --heading-green:#3d7a22;
  --wood:#3a2418;
  --numeral:#f1f0ec;
}
*{margin:0;padding:0;box-sizing:border-box}
html,body{width:1200px;height:675px;overflow:hidden;background:var(--bg)}
body{position:relative;font-family:"Open Sans",sans-serif;color:var(--ink)}
.spread{position:absolute;left:24px;top:97px;width:760px;height:480px;display:flex;box-shadow:0 6px 18px rgba(0,0,0,.18)}
.page{position:relative;width:380px;height:480px;overflow:hidden;
  background:linear-gradient(180deg,var(--page-top) 0%,var(--page-mid) 45%,var(--page-low) 100%)}
.page--left{border-right:1px solid rgba(0,0,0,.08)}
.title{position:absolute;left:60px;top:36px;font-family:"Oswald",sans-serif;font-weight:700;line-height:.95;color:var(--title-blue);font-size:38px;letter-spacing:-1px}
.title .year{color:var(--title-green);font-size:44px}
.course-photo{position:absolute;left:282px;top:34px;width:110px;height:110px;border-radius:50%;
  background:radial-gradient(circle at 40% 35%,#8fb9d8 0%,#6f9c4f 55%,#4f7c2c 100%);border:3px solid #fff}
.vertical{position:absolute;font-family:"Oswald",sans-serif;font-weight:500;color:var(--heading-green);
  transform:rotate(-90deg);transform-origin:left top;white-space:nowrap;font-size:30px}
.v-hole{left:18px;top:470px}
.v-team{left:12px;top:190px}
.v-players{left:194px;top:120px}
.list{position:absolute;list-style:none;font-size:7.6px;line-height:1.55;font-style:italic}
.list li::before{content:"•  "}
.list--hole1{left:66px;top:160px}
.list--hole2{left:170px;top:160px}
.list--hole3{left:270px;top:190px}
.list--team{left:52px;top:28px;font-style:normal;font-weight:600}
.list--players{left:242px;top:28px;width:132px;font-style:normal;font-weight:600}
.thanks-dot{position:absolute;left:120px;top:330px;width:90px;height:90px;border-radius:50%;background:#5d8a35}
.thanks{position:absolute;left:40px;top:420px;font-style:italic;font-size:10px}
.ad-box{position:absolute;left:40px;top:436px;width:220px;height:34px;background:#fff;border:1px solid #9db78a;border-radius:4px;
  font-size:7px;padding:8px 10px}
.cover{position:absolute;left:806px;top:97px;width:370px;height:480px;background:var(--wood);overflow:hidden;box-shadow:0 6px 18px rgba(0,0,0,.25)}
.cover svg{position:absolute;left:0;top:0}
.numeral{position:absolute;font-family:"Abril Fatface",serif;color:var(--numeral);line-height:1}
.n-2{left:24px;top:228px;font-size:110px}
.n-0{left:22px;top:330px;font-size:130px}
.n-21{left:160px;top:345px;font-size:120px;letter-spacing:-3px}
</style>
</head>
<body>
<section class="spread">
  <article class="page page--left">
    <h1 class="title">GOLF <span class="year">2020</span><br>TOURNAMENT</h1>
    <div class="course-photo" role="img" aria-label="Photo of the golf course fairway"></div>
    <h2 class="vertical v-hole">Hole Sponsors</h2>
    <ul class="list list--hole1">
      <li>Birch Lane Art Studio</li><li>Tom and Rita Dalby</li><li>Owen &amp; Maren Pruitt</li>
      <li>Fieldstone Print Co.</li><li>Hollis &amp; Vane Diner</li><li>Nora &amp; Glen Whitcomb</li><li>Elton &amp; Faye Marsh</li>
    </ul>
    <ul class="list list--hole2">
      <li>Carden Ivy Lathrop</li><li>Dane &amp; Lacey Orwell</li><li>Keel Builders LLC</li>
      <li>Ridgeline Trail Supply</li><li>Milo Brandt</li><li>Reid Calloway</li><li>Cole &amp; Jenna Ashby</li>
    </ul>
    <ul class="list list--hole3">
      <li>Vance Tolliver</li><li>Loopform Plastics</li><li>Grant &amp; Della Pierce</li>
      <li>Northgate Realty Team</li><li>Hal &amp; Ruth Emery</li><li>Beau &amp; Lila Harmon</li><li>Wade &amp; Tessa Quill</li>
    </ul>
  </article>
  <article class="page page--right">
    <h2 class="vertical v-team">Team Sponsor</h2>
    <ul class="list list--team">
      <li>Summit Roofing</li><li>Copperline Auto Team</li><li>Meadow State Bank Team</li>
      <li>Halvorsen Team</li><li>Greenacre Lawn &amp; Garden</li><li>Brightcoat Paints</li>
    </ul>
    <h2 class="vertical v-players">Players</h2>
    <ul class="list list--players">
      <li>Lane Whitfield, Rory Sabin, Jett Colter, Bo Mann</li>
      <li>Gus Barlow, Jon Hale, Jim Brody, Walt Becker</li>
      <li>Bert Tilden, Jay Garner, Jed Moss, Len Jarvis</li>
      <li>Mack Larue, Ted Porter, Kip Bristow, Jess Penrose</li>
      <li>Art Dalby, Rita Dalby, Hollis Dean, Mark Waverly</li>
    </ul>
    <div class="thanks-dot" role="img" aria-label="Round photo of tournament players"></div>
    <p class="thanks">Thank you to our sponsors</p>
    <div class="ad-box">Helping small business grow since day one</div>
  </article>
</section>

<section class="cover">
  <svg width="370" height="480" viewBox="0 0 370 480">
    <g role="img" aria-label="Photo of signed camp banners from past summers">
      <rect x="10" y="30" width="105" height="50" rx="14" fill="#c7692c"/>
      <rect x="125" y="22" width="105" height="56" rx="14" fill="#2f6b2a"/>
      <rect x="245" y="25" width="110" height="50" rx="14" fill="#4a3c1f"/>
      <rect x="8" y="108" width="112" height="66" rx="16" fill="#e29a4e"/>
      <rect x="128" y="98" width="112" height="62" rx="14" fill="#f1a534"/>
      <rect x="250" y="95" width="110" height="56" rx="14" fill="#3b2b22" stroke="#5a463a"/>
      <rect x="118" y="185" width="118" height="60" rx="16" fill="#a9c4e0"/>
      <rect x="248" y="180" width="110" height="64" rx="14" fill="#f0cc2a"/>
    </g>
  </svg>
  <div class="numeral n-2">2</div>
  <div class="numeral n-0">0</div>
  <div class="numeral n-21">21</div>
</section>
</body>
</html>
```